The Copper Kite Website Redesign

I want a new design and website for www.thecopperkitebrookvale.com where part of the home page includes our daily specials from our POS Toast to be pulled from API. I have included photos and links to give you a better feel for the style of our restaurant.

Coding

Coded - Design and coding required

```html
<!DOCTYPE html>
<html lang="en">
<head>
<meta charset="utf-8">
<title>The Copper Kite</title>
<link href="https://fonts.googleapis.com/css2?family=Mouse+Memoirs&family=Dancing+Script:wght@600&family=Lato:wght@400;700&display=swap" rel="stylesheet">
<style>
:root{
  --orange:#ff7a00;
  --orange-btn:#ff6a00;
  --ink:#1b1b1b;
  --text:#3a3a3a;
  --muted:#8a8a8a;
  --cream:#fefef1;
  --white:#ffffff;
  --line:#d9d9d9;
}
*{margin:0;padding:0;box-sizing:border-box}
html,body{width:1200px;height:4035px;overflow:hidden}
body{position:relative;background:var(--white);font-family:'Lato',sans-serif;color:var(--text)}
.abs{position:absolute}
.display{font-family:'Mouse Memoirs',sans-serif;font-weight:400;color:var(--ink)}
.btn{position:absolute;display:flex;align-items:center;justify-content:center;border-radius:22px;font-family:'Mouse Memoirs',sans-serif;font-size:20px;box-shadow:0 5px 8px rgba(0,0,0,.25)}
.btn--orange{background:var(--orange-btn);color:var(--white)}
.btn--white{background:var(--white);color:var(--ink)}
.rule{position:absolute;height:4px;background:var(--ink)}
.rule--thin{height:2px}
.rule--white{background:var(--white)}
.photo{position:absolute}

/* header */
.site-header{position:absolute;left:0;top:0;width:1200px;height:103px;background:var(--white)}
.brand{position:absolute;left:110px;top:28px;font-family:'Mouse Memoirs',sans-serif;font-size:46px;color:var(--ink);line-height:1}
.nav{position:absolute;top:38px;left:450px;display:flex;gap:40px;font-family:'Mouse Memoirs',sans-serif;font-size:22px;color:var(--ink)}
.nav .active{color:var(--orange)}
.call-box{position:absolute;right:0;top:0;width:245px;height:102px;background:var(--orange);clip-path:polygon(38px 0,100% 0,100% 100%,0 100%);color:var(--white);font-family:'Mouse Memoirs',sans-serif}
.call-box .label{position:absolute;left:72px;top:12px;font-size:22px;display:flex;align-items:center;gap:8px}
.call-box .num{position:absolute;left:62px;top:44px;font-size:38px}

/* hero */
.hero{position:absolute;left:0;top:103px;width:1200px;height:650px;background:linear-gradient(110deg,#2a2622 0%,#4a3a2c 40%,#b8601e 65%,#8a4a1c 85%,#3a2a20 100%)}
.hero-text{color:var(--white)}
.hero .welcome{position:absolute;left:110px;top:110px;font-family:'Mouse Memoirs',sans-serif;font-size:38px}
.hero .title{position:absolute;left:108px;top:165px;font-family:'Mouse Memoirs',sans-serif;font-size:100px;line-height:1}
.hero .lede{position:absolute;left:110px;top:334px;width:420px;font-size:15px;font-weight:700;line-height:29px}

/* sections */
.section-title{position:absolute;font-family:'Mouse Memoirs',sans-serif;font-size:64px;color:var(--ink);line-height:1}
.section-kicker{position:absolute;font-family:'Dancing Script',cursive;font-size:17px;color:var(--orange)}
.about-copy{position:absolute;left:667px;top:942px;width:421px;font-size:14px;line-height:29px;text-align:justify}

/* menu */
.menu-section{position:absolute;left:0;top:1550px;width:1200px;height:1177px;background:var(--cream)}
.dish{position:absolute;width:260px}
.dish .stars{color:var(--orange);font-size:15px;letter-spacing:1px}
.dish h3{font-size:20px;font-weight:400;color:var(--ink);margin-top:6px}
.dish .tag{font-size:14px;color:var(--muted);margin-top:8px}
.dish .desc{font-size:11.5px;color:var(--muted);line-height:25px;margin-top:4px}
.dish .more{display:flex;align-items:flex-end;gap:8px;margin-top:-2px;color:var(--orange);font-size:18px}
.dish .more .dots{flex:0 0 130px;border-bottom:2px dotted var(--orange);margin-bottom:5px}
.dish-photo{position:absolute;width:171px;height:178px;border-radius:6px}

/* specials */
.specials{position:absolute;left:0;top:2727px;width:1200px;height:881px;background:var(--orange)}
.specials p{font-size:15px;font-weight:700;color:var(--ink);line-height:29px}
.caption{position:absolute;font-family:'Mouse Memoirs',sans-serif;font-size:26px;color:var(--ink)}

/* footer */
.footer-col h4{font-family:'Mouse Memoirs',sans-serif;font-size:28px;font-weight:400;color:var(--ink);margin-bottom:16px}
.footer-col li{list-style:none;font-size:15px;color:var(--ink);line-height:34px}
.contact-row{display:flex;align-items:flex-start;gap:14px;font-size:15px;color:var(--ink);line-height:26px;margin-bottom:22px}
.icon-dot{flex:0 0 32px;height:32px;border-radius:50%;background:var(--orange);display:flex;align-items:center;justify-content:center}
.social{position:absolute;width:28px;height:28px;border-radius:50%;border:2px solid var(--orange)}
</style>
</head>
<body>

<header class="site-header">
  <div class="brand">The Copper Kite</div>
  <nav class="nav">
    <span class="active">Home</span><span>Menu</span><span>About Us</span><span>Retail</span><span>Press</span><span>Contact Us</span>
  </nav>
  <div class="call-box">
    <div class="label">
      <svg width="22" height="22" viewBox="0 0 24 24"><circle cx="12" cy="12" r="11" fill="#fff"/><path d="M8 6c1 0 1.5 2.5 1.5 3s-1 1-1 1.5 2 3 3 3 1-1 1.5-1 3 .5 3 1.5-1.5 2-2.5 2c-3 0-7-4-7-7 0-1 1-3 1.5-3z" fill="#ff7a00"/></svg>
      Call Us Today
    </div>
    <div class="num">(312) 555-0148</div>
  </div>
</header>

<section class="hero">
  <div class="photo" role="img" aria-label="Close-up of seasoned fries beside a jar of sauce" style="inset:0;background:linear-gradient(110deg,rgba(0,0,0,.35),rgba(0,0,0,0) 55%)"></div>
  <div class="hero-text">
    <div class="welcome">Welcome to</div>
    <div class="title">The Copper Kite</div>
    <p class="lede">The doors of The Copper Kite: a finer diner were eagerly thrown open for the first time on December 28th 2004.</p>
  </div>
  <div class="btn btn--white" style="left:111px;top:414px;width:116px;height:40px;box-shadow:none">Get Started</div>
  <div class="rule rule--white" style="left:0;top:490px;width:173px"></div>
  <div class="rule rule--white" style="left:0;top:513px;width:283px"></div>
  <div class="rule rule--white" style="left:0;top:533px;width:160px"></div>
  <svg class="abs" style="left:0;top:520px" width="1200" height="130" viewBox="0 0 1200 130" preserveAspectRatio="none">
    <polygon fill="#fff" points="0,70 40,62 80,74 120,58 170,68 220,60 260,72 320,56 380,66 430,58 480,70 540,60 600,72 660,56 720,66 780,50 840,62 900,48 960,58 1020,44 1080,54 1140,40 1200,46 1200,130 0,130"/>
  </svg>
</section>

<!-- about -->
<svg class="abs" style="left:102px;top:816px" width="44" height="44" viewBox="0 0 44 44" aria-hidden="true"><circle cx="22" cy="22" r="16" fill="none" stroke="#1b1b1b" stroke-width="4"/></svg>
<h2 class="section-title" style="left:390px;top:785px">About The Copper Kite</h2>
<div class="section-kicker" style="left:390px;top:858px">Who We Are</div>
<div class="rule rule--thin" style="left:640px;top:860px;width:115px"></div>
<div class="rule rule--thin" style="left:640px;top:870px;width:170px"></div>
<div class="rule rule--thin" style="left:640px;top:880px;width:115px"></div>

<div class="photo" role="img" aria-label="Diner storefront with the restaurant sign over yellow tiles" style="left:111px;top:952px;width:299px;height:328px;background:linear-gradient(160deg,#8a8fd0,#b99ad8 45%,#d8c840 75%,#6a6a5a)"></div>
<div class="photo" role="img" aria-label="Plate of waffles with fruit on a red diner counter" style="left:319px;top:1070px;width:298px;height:408px;background:linear-gradient(170deg,#c84040,#6a3a30 40%,#9a6a40 70%,#3a2a22)"></div>

<p class="about-copy">We welcomed our first customers and started our magnificent life as a business that continues on through today. Along with our beloved and inquisitive customers came the many questions of our origin. The most important of which we will address right here and now… "Why?" they asked "Why did you name your restaurant The Copper Kite?" We always swore we would make up some exciting folklore tale of the origin of our now-venerated name, but we never quite came up with a story glorious enough to do justice to the wonderment. So now, in a moment of honesty, for the eyes of our website visitors ONLY, we give you the real skinny on the naming of our restaurant. We had been toiling arduously at the restaurant for many weeks when we knew it was time to give our creation a name… We took a small respite from our renovations and decided to brainstorm over a few cocktails.</p>
<div class="btn btn--orange" style="left:667px;top:1401px;width:117px;height:40px">Read More</div>
<div class="rule" style="left:1040px;top:1445px;width:160px"></div>
<div class="rule" style="left:1018px;top:1465px;width:182px"></div>
<div class="rule" style="left:998px;top:1486px;width:202px"></div>

<!-- menu -->
<section class="menu-section">
  <h2 class="section-title" style="left:513px;top:65px">Our Menu</h2>
  <div class="section-kicker" style="left:513px;top:140px">Menu</div>
  <div class="rule rule--thin" style="left:640px;top:142px;width:115px"></div>
  <div class="rule rule--thin" style="left:640px;top:152px;width:170px"></div>
  <div class="rule rule--thin" style="left:640px;top:162px;width:115px"></div>

  <div class="abs" style="left:599px;top:222px;width:1px;height:753px;background:var(--line)"></div>
  <div class="abs" style="left:111px;top:462px;width:977px;height:1px;background:var(--line)"></div>
  <div class="abs" style="left:111px;top:717px;width:977px;height:1px;background:var(--line)"></div>

  <div class="dish-photo" role="img" aria-label="Fried eggs with broccoli and bacon" style="left:111px;top:240px;background:linear-gradient(135deg,#f4e9c8,#e8b030 40%,#3a7a30 70%,#2a2a2a)"></div>
  <div class="dish" style="left:303px;top:244px"><div class="stars">★★★★★</div><h3>Green Eggs and Ham</h3><div class="tag">Duis aute irure dolor</div><div class="desc">Poblano Pesto and Jack Cheese Rumbled with Eggs Sidled by Seared City Ham</div><div class="more"><span class="dots"></span>View More</div></div>

  <div class="dish-photo" role="img" aria-label="Bowl of fruit topped with ice cream" style="left:666px;top:240px;background:linear-gradient(135deg,#8a8aa0,#f0d060 45%,#e89030 70%,#5a5a6a)"></div>
  <div class="dish" style="left:857px;top:244px"><div class="stars">★★★★★</div><h3>Veggie Rumble</h3><div class="tag">Excepteur sint occaecat</div><div class="desc">Red Pepper, Carrots, Mushrooms, Peas, Spinach and Provolone.</div><div class="more"><span class="dots"></span>View More</div></div>

  <div class="dish-photo" role="img" aria-label="Stack of crispy hash brown patties" style="left:111px;top:501px;background:linear-gradient(135deg,#e8a850,#c87830 50%,#a05a20)"></div>
  <div class="dish" style="left:303px;top:505px"><div class="stars">★★★★★</div><h3>The Boot- Milano's</h3><div class="tag">Deserunt mollit anim</div><div class="desc">A Rumble of Eggs with Fresh Mozzarella, Basil, Tomatoes, &amp; Green Olives</div><div class="more"><span class="dots"></span>View More</div></div>

  <div class="dish-photo" role="img" aria-label="Fried eggs with mushrooms and herbs" style="left:666px;top:501px;background:linear-gradient(135deg,#d8d0c0,#f0c040 40%,#b09a80 70%,#7a6a5a)"></div>
  <div class="dish" style="left:857px;top:505px"><div class="stars">★★★★★</div><h3>The Forager</h3><div class="tag">Quis nostrud exercitation</div><div class="desc">Mushrooms, Caramelized Onion, Smoked Gouda &amp; Greens Rumbled with Eggs</div><div class="more"><span class="dots"></span>View More</div></div>

  <div class="dish-photo" role="img" aria-label="Poached egg on a toasted muffin" style="left:111px;top:757px;background:linear-gradient(135deg,#3a4a3a,#f0c030 45%,#d88a30 70%,#2a2a2a)"></div>
  <div class="dish" style="left:303px;top:761px"><div class="stars">★★★★★</div><h3>Huevos Rancheros</h3><div class="tag">Occaecat cupidatat non</div><div class="desc">Two Eggs Any Style, Crispy Flour Tortilla, Black Beans, Jack Cheese</div><div class="more"><span class="dots"></span>View More</div></div>

  <div class="dish-photo" role="img" aria-label="Fried eggs with toast on a dark plate" style="left:666px;top:757px;background:linear-gradient(135deg,#c88a40,#2a2a2a 45%,#f0f0e8 70%,#e8a020)"></div>
  <div class="dish" style="left:857px;top:761px"><div class="stars">★★★★★</div><h3>Cowboy Carver</h3><div class="tag">Dolor in reprehenderit</div><div class="desc">Seared Flank Steak Straddlin' a Wildwest Sauce, Two Eggs Fried</div><div class="more"><span class="dots"></span>View More</div></div>

  <div class="btn btn--orange" style="left:534px;top:1044px;width:134px;height:46px;font-size:22px">View More</div>
  <div class="rule" style="left:0;top:1060px;width:135px"></div>
  <div class="rule" style="left:0;top:1082px;width:242px"></div>
  <div class="rule" style="left:0;top:1103px;width:120px"></div>
</section>

<!-- daily specials -->
<section class="specials">
  <h2 class="section-title" style="left:110px;top:98px">Daily Specials</h2>
  <div class="section-kicker" style="left:110px;top:178px;color:var(--ink)">Special</div>
  <div class="rule rule--thin" style="left:310px;top:175px;width:115px"></div>
  <div class="rule rule--thin" style="left:310px;top:185px;width:170px"></div>
  <div class="rule rule--thin" style="left:310px;top:195px;width:115px"></div>
  <p class="abs" style="left:110px;top:221px">Hours: Saturday through Sunday -8 8-m- until 8 p-m-<br>Please call for any holiday hour's information-</p>

  <div class="photo" role="img" aria-label="Poached eggs with avocado and salmon on a muffin" style="left:111px;top:305px;width:448px;height:448px;background:linear-gradient(150deg,#5a7a3a,#e8c040 40%,#e88a50 65%,#3a3a3a)"></div>
  <div class="caption" style="left:108px;top:775px">Crab Cake &amp; Eggs</div>
  <svg class="abs" style="left:536px;top:786px" width="14" height="14" viewBox="0 0 14 14"><path d="M1 7h11M8 3l4 4-4 4" stroke="#1b1b1b" stroke-width="2" fill="none"/></svg>

  <div class="photo" role="img" aria-label="Lobster roll in a toasted bun" style="left:641px;top:98px;width:447px;height:448px;background:linear-gradient(170deg,#6a4a30,#d88a50 35%,#e86a40 55%,#c8905a 75%,#3a2a20)"></div>
  <div class="caption" style="left:638px;top:565px">Slacker Special</div>
  <svg class="abs" style="left:1073px;top:576px" width="14" height="14" viewBox="0 0 14 14"><path d="M1 7h11M8 3l4 4-4 4" stroke="#1b1b1b" stroke-width="2" fill="none"/></svg>
  <p class="abs" style="left:641px;top:626px;width:447px;font-weight:400;font-size:14px;text-align:justify">"I would never eat at a place called The Copper Kite" and our family and friends thinking that we had a failure-wish, but we think with our unusual name we weeded out the closed-minded few and impressed the adventurous many with a bona fide finer diner.</p>
  <div class="btn btn--white" style="left:641px;top:755px;width:115px;height:40px">Buy Now</div>
  <div class="rule" style="left:1003px;top:843px;width:197px"></div>
  <div class="rule" style="left:988px;top:862px;width:212px"></div>
  <div class="rule" style="left:966px;top:878px;width:234px"></div>
</section>

<!-- footer -->
<footer>
  <div class="abs display" style="left:110px;top:3712px;font-size:48px;line-height:1">The Copper Kite</div>
  <span class="social" style="left:131px;top:3816px;background:var(--orange)"></span>
  <span class="social" style="left:179px;top:3816px"></span>
  <span class="social" style="left:228px;top:3816px"></span>
  <span class="social" style="left:276px;top:3816px"></span>

  <div class="footer-col abs" style="left:421px;top:3680px"><h4>Quick Links</h4><ul><li>Home</li><li>About</li><li>Menu</li><li>Press</li><li>Contact us</li></ul></div>
  <div class="footer-col abs" style="left:641px;top:3680px"><h4>Help Links</h4><ul><li>FAQ</li><li>Terms of use</li><li>Privacy Policy</li><li>Support Links</li><li>Conditions</li></ul></div>
  <div class="footer-col abs" style="left:846px;top:3680px;width:260px"><h4>Contact Us</h4>
    <div class="contact-row"><span class="icon-dot"><svg width="14" height="18" viewBox="0 0 14 18"><path d="M7 0a7 7 0 0 0-7 7c0 5 7 11 7 11s7-6 7-11a7 7 0 0 0-7-7z" fill="#fff"/><circle cx="7" cy="7" r="2.5" fill="#ff7a00"/></svg></span><span>4180 Harbor Lane Avenue<br>Brookvale, Oregon 97015</span></div>
    <div class="contact-row"><span class="icon-dot"><svg width="16" height="16" viewBox="0 0 24 24"><path d="M6 2c2 0 3 5 3 6s-2 2-2 3 4 6 6 6 2-2 3-2 6 1 6 3-3 4-5 4C10 22 2 14 2 7c0-2 2-5 4-5z" fill="#fff"/></svg></span><span>(312) 555-0148</span></div>
    <div class="contact-row"><span class="icon-dot"><svg width="16" height="12" viewBox="0 0 16 12"><rect x="0" y="0" width="16" height="12" rx="1.5" fill="#fff"/><path d="M1 1l7 6 7-6" stroke="#ff7a00" stroke-width="1.5" fill="none"/></svg></span><span>eat@thecopperkitebrookvale.com</span></div>
  </div>

  <div class="abs" style="left:111px;top:3930px;width:977px;height:1px;background:var(--line)"></div>
  <div class="abs" style="left:0;top:3966px;width:1200px;text-align:center;font-size:15px;font-weight:700;color:var(--ink)">Copyrights@2025.The Copper Kite.All Rights Reserved</div>
</footer>

</body>
</html>
```